Varelko App for Smart Devices IoT WiFi Electronic

Varelko is a siren manufacturer. This application is used for the company's products that have a Wi-Fi connection and an internet connection, which can be configured and activated remotely through this application. In addition, this application is used to activate the siren at specific times for the start and end of shifts in companies and schools. Users will be siren installers and IT or HR managers.
In addition to activating motorized sirens timers, some siren models have speakers and allow you to play TTS (text to speech) audio, audio recorded by the user on the phone and upload audio (mp3) with playlist programming with start and end times.
Application screens: home with dashboard (one dashboard for each category). Device categories: timers, speakers, motorized siren. Screen for requesting evaluation in the Play Store. Screen for registering the user profile. Screen for registering devices according to their category (timers, speakers, motorized siren). Screen for registering device groups. Screen for pairing the device on the client's Wi-Fi network. Screen for registering activation times. Screen for uploading MP3 audios. Screen for registering playlists with audio selection, start and end times. Screen for recording audio for later sending to the speakers. Screen for converting text to speech and sending to the speakers. It is important to have a time picker with the day of the week to program the activation times and playlist.

Target Market(s)

Schools, Companies and Stores.

Industry/Entity Type

IoT

Font styles to use
Sans Serif
Other font styles liked:
• roboto

Colors
FFC000
F8CF3A
FAE287
FDF2CF
FEFAEE

Requirements
Must have
• time picker with weekdays for timer programming feature.
Nice to have
• app review request screen on play store

```html
<!DOCTYPE html>
<html lang="en">
<head>
<meta charset="utf-8">
<title>Varelko Siren Control App</title>
<link href="https://fonts.googleapis.com/css2?family=Montserrat:wght@500;600;700&family=Roboto:wght@400;500;700&display=swap" rel="stylesheet">
<style>
  :root{
    --amber:#FFC000;
    --gold:#F8CF3A;
    --butter:#FAE287;
    --cream:#FDF2CF;
    --ivory:#FEFAEE;
    --ink:#1f1f1f;
    --muted:#8a8a8a;
    --line:#ececec;
    --white:#ffffff;
  }
  *{box-sizing:border-box;margin:0;padding:0}
  html,body{width:1200px;height:3394px;overflow:hidden}
  body{position:relative;background:var(--white);font-family:"Roboto",sans-serif;color:var(--ink)}
  .backdrop{position:absolute;inset:0;width:1200px;height:3394px}
  .abs{position:absolute}

  .brand-mark{position:absolute;left:645px;top:228px;font-family:"Montserrat",sans-serif;font-weight:600;font-size:82px;color:var(--white);letter-spacing:1px}
  .hero-title{position:absolute;left:598px;top:506px;font-family:"Montserrat",sans-serif;font-weight:600;font-size:23px;letter-spacing:4.5px;color:var(--ink)}
  .hero-copy{position:absolute;left:598px;top:557px;width:440px;font-family:"Montserrat",sans-serif;font-size:11.5px;line-height:13px;letter-spacing:1.6px;color:var(--ink)}
  .store-badge{position:absolute;top:705px;width:173px;height:56px;background:#0d0d0d;border-radius:8px}

  .section-title{position:absolute;width:420px;text-align:center;font-family:"Montserrat",sans-serif;font-weight:700;font-size:37px;letter-spacing:9px;color:var(--white)}

  .screen{position:absolute;overflow:hidden;border-radius:34px;background:var(--white);box-shadow:0 10px 30px rgba(120,80,0,.18)}
  .status{position:absolute;left:0;right:0;top:0;height:30px;font-size:10px;font-weight:600;padding:12px 22px 0}
  .status .time{float:left}
  .status .icons{float:right;display:flex;gap:3px;align-items:center}
  .status .icons i{display:block;background:var(--ink);border-radius:1px}
  .wordmark{position:absolute;left:0;right:0;text-align:center;font-family:"Montserrat",sans-serif;font-weight:600;color:var(--white)}
  .screen-heading{position:absolute;left:0;right:0;text-align:center;font-weight:700;color:var(--ink)}
  .screen-sub{position:absolute;left:0;right:0;text-align:center;font-size:7.5px;color:#444}
  .sheet{position:absolute;left:0;right:0;bottom:0;background:var(--white);border-radius:26px 26px 0 0}
  .field-label{position:absolute;font-size:7.5px;color:#555}
  .field{position:absolute;height:31px;border:1px solid var(--line);border-radius:6px;font-size:8.5px;font-weight:500;padding:10px 10px 0;color:var(--ink)}
  .field .eye{position:absolute;right:9px;top:11px;width:10px;height:7px;border:1px solid #bbb;border-radius:50%}
  .btn{position:absolute;height:31px;background:var(--amber);border-radius:6px;color:var(--white);font-size:8.5px;font-weight:500;text-align:center;line-height:31px}
  .foot-note{position:absolute;left:0;right:0;text-align:center;font-size:7.5px;color:#444}
  .foot-note b{color:var(--amber);font-weight:500}

  .dash-card{position:absolute;left:16px;width:283px;border-radius:8px;background:var(--white);box-shadow:0 4px 12px rgba(0,0,0,.1)}
  .dash-card .art{position:absolute;left:20px;top:50%;width:46px;height:46px;margin-top:-23px;border-radius:50%}
  .dash-card .name{position:absolute;left:92px;top:50%;transform:translateY(-50%);font-size:15px;font-weight:500;color:#333}
  .dash-card .go{position:absolute;right:20px;top:50%;width:22px;height:22px;margin-top:-11px;border:1.5px solid var(--gold);border-radius:4px}
  .dash-card .go svg{display:block}
  .nav-bar{position:absolute;left:10px;right:10px;top:616px;height:58px;background:var(--amber);border-radius:14px;display:flex;justify-content:space-around;align-items:center}
  .nav-item{text-align:center;font-size:6.5px;color:var(--white);opacity:.8}
  .nav-item.active{opacity:1;font-weight:500}
  .nav-item svg{display:block;margin:0 auto 3px}

  .group-title{position:absolute;left:18px;font-size:11px;font-weight:500;color:var(--ink)}
  .opt-title{position:absolute;left:18px;font-size:10px;font-weight:500}
  .opt-desc{position:absolute;left:18px;font-size:6.8px;color:var(--muted)}
  .toggle{position:absolute;right:20px;width:38px;height:21px;border-radius:11px;background:#e4e4e4;border:1px solid #cfcfcf}
  .toggle::after{content:"";position:absolute;left:2px;top:2px;width:15px;height:15px;border-radius:50%;background:var(--white);box-shadow:0 1px 2px rgba(0,0,0,.3)}
  .toggle.on{background:var(--amber);border-color:var(--amber)}
  .toggle.on::after{left:19px}
  .weekdays{position:absolute;left:12px;right:12px;display:flex;justify-content:space-between}
  .day{width:34px;text-align:center;font-size:5.5px;color:var(--amber)}
  .day span{display:block;width:16px;height:16px;margin:0 auto 3px;border:1px solid var(--amber);border-radius:50%;font-size:8px;line-height:14px}
  .day.off{color:#bbb}.day.off span{border-color:#ccc}
  .radio-row{position:absolute;left:18px;display:flex;gap:18px;font-size:8px;color:#bbb}
  .radio-row label{display:flex;align-items:center;gap:4px}
  .radio-row i{width:9px;height:9px;border:1px solid #ccc;border-radius:50%;display:block}
  .radio-row .sel{color:var(--amber)}
  .radio-row .sel i{border-color:var(--amber);background:radial-gradient(var(--amber) 45%,transparent 50%)}
</style>
</head>
<body>

<svg class="backdrop" viewBox="0 0 1200 3394" aria-hidden="true">
  <rect width="1200" height="3394" fill="var(--white)"/>
  <path d="M0 0H1200V540C1010 470 820 420 640 428C420 438 200 540 0 674Z" fill="var(--amber)"/>
  <path d="M0 2858C200 3040 420 3180 640 3190C860 3200 1040 3130 1200 3080V3394H0Z" fill="var(--amber)"/>
  <circle cx="353" cy="1231" r="207" fill="var(--amber)"/>
  <circle cx="853" cy="1231" r="207" fill="var(--amber)"/>
  <circle cx="353" cy="2328" r="207" fill="var(--amber)"/>
  <circle cx="853" cy="2328" r="207" fill="var(--amber)"/>
</svg>

<!-- hero -->
<div class="screen splash-screen" style="left:184px;top:228px;width:330px;height:582px;background:linear-gradient(180deg,var(--cream) 0%,var(--butter) 45%,var(--gold) 75%,var(--amber) 100%)">
  <div class="status"><span class="time">09:41</span><span class="icons"><i style="width:10px;height:6px"></i><i style="width:8px;height:6px"></i><i style="width:14px;height:7px"></i></span></div>
  <div class="wordmark" style="top:232px;font-size:42px;opacity:.9">varelko</div>
  <svg class="abs" style="left:0;top:440px" width="330" height="142" viewBox="0 0 330 142" aria-hidden="true">
    <path d="M0 80C60 50 120 70 170 50C230 25 290 30 330 10V142H0Z" fill="var(--amber)"/>
  </svg>
  <svg class="abs" style="left:142px;top:448px" width="46" height="46" viewBox="0 0 46 46" aria-hidden="true">
    <circle cx="23" cy="23" r="22" fill="var(--white)"/>
    <path d="M19 15L28 23L19 31" fill="none" stroke="var(--amber)" stroke-width="3" stroke-linecap="round" stroke-linejoin="round"/>
  </svg>
</div>

<div class="brand-mark">varelko</div>
<h1 class="hero-title">Varelko Siren Control App</h1>
<p class="hero-copy">Varelko Siren Control App industries, schools, aur companies ke liye ek smart solution hai, jo Wi-Fi se connected sirens ko remotely activate aur manage karne ki sahulat deta hai. Users asaani se sirens ke activation times schedule kar sakte hain, audio playlists set kar sakte hain, aur text-to-speech (TTS) features ka bhi faida utha sakte hain. Is app ke zariye, siren management ab aur bhi aasaan aur efficient hai!</p>
<div class="store-badge" style="left:602px" role="img" aria-label="First mobile store download badge"></div>
<div class="store-badge" style="left:784px" role="img" aria-label="Second mobile store download badge"></div>

<!-- login -->
<div class="section-title" style="left:143px;top:1130px">Login Screen</div>
<div class="screen login-screen" style="left:201px;top:1209px;width:299px;height:648px;background:linear-gradient(180deg,var(--cream) 0%,var(--butter) 45%,var(--gold) 100%)">
  <div class="status"><span class="time">09:41</span><span class="icons"><i style="width:8px;height:5px"></i><i style="width:7px;height:5px"></i><i style="width:12px;height:6px"></i></span></div>
  <div class="wordmark" style="top:220px;font-size:44px">varelko</div>
  <div class="screen-heading" style="top:298px;font-size:20px">Get Started now</div>
  <div class="screen-sub" style="top:328px">Create an account or log in to explore about our app</div>
  <div class="sheet" style="top:365px">
    <div class="field-label" style="left:16px;top:35px">User Name / Email</div>
    <div class="field" style="left:16px;top:49px;width:267px">Enter User Name</div>
    <div class="field-label" style="left:16px;top:93px">Password</div>
    <div class="field" style="left:16px;top:103px;width:267px">•••••••<span class="eye"></span></div>
    <div class="abs" style="left:18px;top:153px;width:8px;height:8px;border:1px solid #888;border-radius:1px"></div>
    <div class="field-label" style="left:31px;top:152px">Remember me</div>
    <div class="field-label" style="right:16px;top:152px;color:#3b6fe0">Forgot Password ?</div>
    <div class="btn" style="left:16px;top:192px;width:267px">Log In</div>
    <div class="foot-note" style="top:241px">Don't have an account? <b>Sign Up</b></div>
  </div>
</div>

<!-- registration -->
<div class="section-title" style="left:643px;top:1128px">Registration</div>
<div class="screen register-screen" style="left:705px;top:1209px;width:299px;height:648px;background:linear-gradient(180deg,var(--cream) 0%,var(--butter) 40%,var(--gold) 100%)">
  <div class="status"><span class="time">09:41</span><span class="icons"><i style="width:8px;height:5px"></i><i style="width:7px;height:5px"></i><i style="width:12px;height:6px"></i></span></div>
  <div class="wordmark" style="top:128px;font-size:44px">varelko</div>
  <div class="screen-heading" style="top:198px;font-size:20px">Sign Up</div>
  <div class="screen-sub" style="top:228px">Create an account to continue!</div>
  <div class="sheet" style="top:273px">
    <div class="field-label" style="left:16px;top:40px">First Name</div>
    <div class="field" style="left:16px;top:53px;width:129px">Mara</div>
    <div class="field-label" style="left:154px;top:40px">Last Name</div>
    <div class="field" style="left:154px;top:53px;width:129px">Kent</div>
    <div class="field-label" style="left:16px;top:99px">Email</div>
    <div class="field" style="left:16px;top:113px;width:267px">mara@mail.test</div>
    <div class="field-label" style="left:16px;top:158px">Password</div>
    <div class="field" style="left:16px;top:172px;width:267px">•••••••<span class="eye"></span></div>
    <div class="field-label" style="left:16px;top:217px">Confirm Password</div>
    <div class="field" style="left:16px;top:232px;width:267px">•••••••<span class="eye"></span></div>
    <div class="btn" style="left:16px;top:287px;width:267px">Register</div>
    <div class="foot-note" style="top:327px">Already have an account? <b>Login</b></div>
  </div>
</div>

<!-- dashboard -->
<div class="section-title" style="left:133px;top:2258px">Dashboard</div>
<div class="screen dashboard-screen" style="left:191px;top:2355px;width:316px;height:685px;background:linear-gradient(180deg,var(--amber) 0%,var(--gold) 12%,var(--butter) 30%,var(--white) 34%)">
  <div class="status"><span class="time">09:41</span><span class="icons"><i style="width:8px;height:5px"></i><i style="width:7px;height:5px"></i><i style="width:12px;height:6px"></i></span></div>
  <svg class="abs" style="left:16px;top:42px" width="16" height="12" viewBox="0 0 16 12" aria-hidden="true"><path d="M0 1H16M0 6H16M0 11H16" stroke="var(--white)" stroke-width="1.6"/></svg>
  <div class="screen-heading" style="top:40px;font-size:14px;font-weight:500;color:var(--white)">Dashboard</div>
  <svg class="abs" style="left:284px;top:40px" width="14" height="16" viewBox="0 0 14 16" aria-hidden="true"><path d="M3 11V7a4 4 0 018 0v4l1.5 1.5h-11Z M5.5 14h3" fill="none" stroke="var(--white)" stroke-width="1.4"/></svg>
  <div class="screen-heading" style="top:89px;font-size:13px;font-weight:500;color:var(--white);line-height:24px">Welcome to<br>Siren Alarm Application</div>
  <div class="abs" style="left:16px;top:154px;width:283px;height:33px;background:var(--white);border-radius:8px;border:1px solid var(--line);font-size:9px;color:#999;padding:11px 0 0 36px">Search
    <svg class="abs" style="left:12px;top:9px" width="14" height="14" viewBox="0 0 14 14" aria-hidden="true"><circle cx="6" cy="6" r="4.5" fill="none" stroke="#999" stroke-width="1.3"/><path d="M9.5 9.5L13 13" stroke="#999" stroke-width="1.3"/></svg>
  </div>
  <div class="dash-card" style="top:213px;height:66px;background:var(--gold)">
    <div class="art" style="background:radial-gradient(circle,var(--white) 40%,#3b7be0 45%)" role="img" aria-label="Alarm clock illustration"></div>
    <div class="name" style="color:var(--white)">Timers</div>
    <div class="go" style="border-color:var(--white)"><svg width="19" height="19" viewBox="0 0 19 19"><path d="M5 9.5H14M10.5 6L14 9.5L10.5 13" fill="none" stroke="var(--white)" stroke-width="1.3"/></svg></div>
  </div>
  <div class="dash-card" style="top:299px;height:73px">
    <div class="art" style="background:linear-gradient(135deg,#7ccf6a,#f5b93a)" role="img" aria-label="Megaphone speaker illustration"></div>
    <div class="name">Speakers</div>
    <div class="go"><svg width="19" height="19" viewBox="0 0 19 19"><path d="M5 9.5H14M10.5 6L14 9.5L10.5 13" fill="none" stroke="var(--gold)" stroke-width="1.3"/></svg></div>
  </div>
  <div class="dash-card" style="top:391px;height:72px">
    <div class="art" style="background:linear-gradient(135deg,#4d86e6,#dfe9fb)" role="img" aria-label="Calendar with tick illustration"></div>
    <div class="name">Motorized Sirens</div>
    <div class="go"><svg width="19" height="19" viewBox="0 0 19 19"><path d="M5 9.5H14M10.5 6L14 9.5L10.5 13" fill="none" stroke="var(--gold)" stroke-width="1.3"/></svg></div>
  </div>
  <nav class="nav-bar">
    <div class="nav-item active"><svg width="14" height="14" viewBox="0 0 14 14"><path d="M2 7L7 2.5L12 7V12.5H2Z" fill="none" stroke="var(--white)" stroke-width="1.4"/></svg>Home<div style="height:2px;background:var(--white);margin-top:6px;width:28px"></div></div>
    <div class="nav-item"><svg width="14" height="14" viewBox="0 0 14 14"><circle cx="7" cy="7" r="5.5" fill="var(--white)"/></svg>Devices</div>
    <div class="nav-item"><svg width="14" height="14" viewBox="0 0 14 14"><path d="M1.5 12.5H12.5M2 10L5.5 6L8 8.5L12 3.5" fill="none" stroke="var(--white)" stroke-width="1.3"/></svg>Settings</div>
    <div class="nav-item"><svg width="14" height="14" viewBox="0 0 14 14"><circle cx="7" cy="5" r="2.8" fill="none" stroke="var(--white)" stroke-width="1.3"/><path d="M2 13C2.5 9.5 11.5 9.5 12 13" fill="none" stroke="var(--white)" stroke-width="1.3"/></svg>Profile</div>
  </nav>
</div>

<!-- set timer -->
<div class="section-title" style="left:643px;top:2256px">Set Timer</div>
<div class="screen timer-screen" style="left:694px;top:2355px;width:315px;height:685px;background:#c9a227">
  <div class="status" style="color:#5a4a1a"><span class="time">09:41</span><span class="icons"><i style="width:8px;height:5px;background:#5a4a1a"></i><i style="width:7px;height:5px;background:#5a4a1a"></i><i style="width:12px;height:6px;background:#5a4a1a"></i></span></div>
  <div class="sheet" style="top:45px;border-radius:18px 18px 0 0">
    <div class="abs" style="left:138px;top:6px;width:40px;height:3px;border-radius:2px;background:var(--amber)"></div>
    <div class="screen-heading" style="top:22px;font-size:13px;font-weight:500">Timers</div>
    <svg class="abs" style="left:279px;top:18px" width="13" height="13" viewBox="0 0 13 13" aria-hidden="true"><path d="M1 1L12 12M12 1L1 12" stroke="var(--amber)" stroke-width="1.6"/></svg>
    <div class="group-title" style="top:50px">Select Device</div>
    <div class="field" style="left:14px;top:69px;width:287px;height:32px">Mara</div>
    <div class="group-title" style="top:138px">Select Date &amp; Time</div>
    <div class="field-label" style="left:18px;top:167px;color:var(--ink);font-size:8px">Start Date</div>
    <div class="field" style="left:14px;top:180px;width:139px;font-weight:400;color:#999;font-size:7.5px">Select Date</div>
    <div class="field-label" style="left:164px;top:167px;color:var(--ink);font-size:8px">End Date</div>
    <div class="field" style="left:160px;top:180px;width:141px;font-weight:400;color:#999;font-size:7.5px">Select Date</div>
    <div class="group-title" style="top:252px">Repeat</div>
    <div class="opt-title" style="top:293px">One Time</div>
    <div class="opt-desc" style="top:310px">It will happen once and then it will be closed.</div>
    <div class="toggle" style="top:294px"></div>
    <div class="opt-title" style="top:349px">Daily</div>
    <div class="opt-desc" style="top:366px">On a daily basis, according to the time you have set.</div>
    <div class="toggle" style="top:349px"></div>
    <div class="opt-title" style="top:405px">Weekly</div>
    <div class="opt-desc" style="top:422px">On a weekly basis, according to the time you have set.</div>
    <div class="toggle" style="top:405px"></div>
    <div class="opt-title" style="top:463px">Custom</div>
    <div class="opt-desc" style="top:480px">In which you can set the day according to your preference.</div>
    <div class="toggle on" style="top:463px"></div>
    <div class="weekdays" style="top:511px">
      <div class="day"><span>M</span>MON</div>
      <div class="day"><span>T</span>TUE</div>
      <div class="day"><span>W</span>WED</div>
      <div class="day"><span>T</span>THU</div>
      <div class="day"><span>F</span>FRI</div>
      <div class="day off"><span>S</span>SAT</div>
      <div class="day off"><span>S</span>SUN</div>
    </div>
    <div class="radio-row" style="top:553px">
      <label><i></i>Once</label>
      <label class="sel"><i></i>Month</label>
      <label><i></i>Year</label>
    </div>
    <div class="btn" style="left:14px;top:577px;width:287px;height:32px;line-height:32px">Save</div>
  </div>
</div>

</body>
</html>
```